Halvex Power

We need a business card for "Halvex power". I have uploaded the logo, the color of the card should be according to the logo "Blackish".
Basically halvex power is a solar company.
Also we would like a sample file in which we can edit the information such names and contact details ourselves
The card would be two sided with following details
1- logo on front and underneath the logo there should be a line saying
"Bright . Steady . Sunlit"
2-website i.e "www.halvexpowerco.com"
3- Icons for Facebook and Instagram that tells the clients we are available on both social sites.
4- name of the person with his/her designation underneath and email address
5-contact number
6- 1-800--- number with the extension number

its up to the designer how he/she places the details,but it must look professional

Industry/Entity Type

Business

Contact Information for Business Card

5-contact number

Requirements
Must have
• 1- logo on front and underneath the logo there should be a line saying
• "Bright . Steady . Sunlit"
• 2-website i.e "www.halvexpowerco.com"
• 3- Icons for Facebook and Instagram that tells the clients we are available on both social sites.
• 4- name of the person with his/her designation underneath and email address
• 5-contact number of the person
• 6- 1-800--- number with the extension number
• 7-card should be in black shade like the logo

```html
<!DOCTYPE html>
<html lang="en">
<head>
<meta charset="utf-8">
<title>Halvex Power — Business Card</title>
<link rel="stylesheet" href="https://fonts.googleapis.com/css2?family=Open+Sans:wght@400;600;700&display=swap">
<style>
  :root {
    --stage: #4a3f3a;
    --card: #141414;
    --card-edge: #1c1c1c;
    --green: #8cc63f;
    --white: #f2f2f2;
    --grey: #9a9a9a;
    --silver: #8d8d8d;
  }
  * { margin: 0; padding: 0; box-sizing: border-box; }
  html, body {
    width: 1200px; height: 864px; overflow: hidden;
    background: var(--stage);
    font-family: "Open Sans", Arial, sans-serif;
  }
  .stage {
    width: 1200px; height: 864px;
    display: flex; align-items: center; justify-content: center; gap: 40px;
  }
  .card {
    position: relative;
    width: 540px; height: 309px;
    background: var(--card);
    border: 1px solid var(--card-edge);
    box-shadow: 0 14px 30px rgba(0,0,0,.45);
  }
  /* Front */
  .card--front .brand-mark {
    position: absolute; left: 0; right: 0; top: 104px;
    text-align: center;
    font-size: 44px; font-weight: 700; color: var(--silver);
    letter-spacing: 1px; white-space: nowrap;
  }
  .card--front .website {
    position: absolute; left: 0; right: 0; top: 192px;
    text-align: center;
    font-size: 12px; color: var(--grey); letter-spacing: 4px;
  }
  /* Back */
  .card--back .brand {
    position: absolute; right: 34px; top: 50px; text-align: right;
  }
  .brand__name {
    font-size: 26px; font-weight: 700; color: var(--green); line-height: 1;
    white-space: nowrap;
  }
  .brand__tagline {
    margin-top: 6px; font-size: 11px; color: var(--white); letter-spacing: .5px;
    white-space: nowrap;
  }
  .person {
    position: absolute; left: 34px; top: 140px;
  }
  .person__name {
    font-size: 16px; font-weight: 700; color: var(--green); letter-spacing: .5px;
  }
  .person__title {
    font-size: 11px; color: var(--grey); letter-spacing: .5px; margin-bottom: 8px;
  }
  .contact-list { list-style: none; }
  .contact-list li {
    display: flex; align-items: center; gap: 8px;
    font-size: 12.5px; color: var(--white); line-height: 18px; white-space: nowrap;
  }
  .contact-list svg { width: 10px; height: 10px; fill: var(--white); flex: none; }
  .divider {
    position: absolute; left: 34px; right: 34px; top: 252px;
    height: 1px; background: var(--white); opacity: .85;
  }
  .social {
    position: absolute; right: 34px; bottom: 16px; display: flex; gap: 8px;
  }
  .social__badge {
    width: 16px; height: 16px; background: var(--green); border-radius: 2px;
  }
</style>
</head>
<body>
<main class="stage">
  <section class="card card--front" aria-label="Card front">
    <div class="brand-mark">Halvex Power</div>
    <div class="website">www.halvexpowerco.com</div>
  </section>

  <section class="card card--back" aria-label="Card back">
    <div class="brand">
      <div class="brand__name">Halvex Power</div>
      <div class="brand__tagline">Bright . Steady . Sunlit</div>
    </div>

    <div class="person">
      <div class="person__name">MARA QUILL</div>
      <div class="person__title">PRESIDENT</div>
      <ul class="contact-list">
        <li>
          <svg viewBox="0 0 10 10"><path d="M2 0.5 L3.6 2.6 L2.8 3.6 Q4 6 6.4 7.2 L7.4 6.4 L9.5 8 L8.4 9.5 Q2.5 8.5 0.5 1.6 Z"/></svg>
          1-800-4816-2037
        </li>
        <li>
          <svg viewBox="0 0 10 10"><path d="M0 2 H10 V8.5 H0 Z M0.6 2.4 L5 5.6 L9.4 2.4 V2.2 H0.6 Z" fill-rule="evenodd"/></svg>
          mara@halvexpowerco.com
        </li>
        <li>
          <svg viewBox="0 0 10 10"><circle cx="5" cy="5" r="4.6" fill="none" stroke="#f2f2f2" stroke-width="1"/><path d="M0.5 5 H9.5 M5 0.4 V9.6" stroke="#f2f2f2" stroke-width="0.8"/></svg>
          www.halvexpowerco.com
        </li>
      </ul>
    </div>

    <div class="divider"></div>

    <div class="social" aria-label="Social profiles">
      <span class="social__badge"></span>
      <span class="social__badge"></span>
    </div>
  </section>
</main>
</body>
</html>
```